sydney wedding photography business needs a business card design

we need a business card design for a sydney based wedding photography and videography business. our business name is :golden hour studio and film. our target clients are 24-35 yrs female. our style is candid, organic, natural, dynamic. we are a team of young photographers and videographers, and help brides to create memories that they will cherish for the rest of their lives. the logo will be provided. we want an elegant design that reflects our style, and also want to give a great impression to our clients that we are one of the best studios in sydney and our brand means quality and premium service.

Target Market(s)

bride to be, 24-35 years old, living in sydney and surrunding areas

Industry/Entity Type

Wedding Photography

Contact Information for Business Card

address: 57 tarrant street, glenmore nsw 2047
mobile: 0431872259
phone: (02) 9163 2408
info@tidewillowstudio.net.au
www.tidewillowstudio.net.au
facebook:tidewillowweddings
instagram:tidewillowweddings

Font styles to use
Serif
Sans Serif

Requirements
Nice to have
• maybe add my slogan"memories beyond eternity" if the layout looks good
Should not have
• no black color, not good idea for wedding biz card

```html
<!DOCTYPE html>
<html lang="en">
<head>
<meta charset="utf-8">
<title>Golden Hour Studio and Film – Business Card</title>
<link rel="stylesheet" href="https://fonts.googleapis.com/css2?family=Source+Sans+3:wght@400;600;700&display=swap">
<style>
  :root {
    --stage: #000000;
    --gold-top: #f7c900;
    --gold-mid: #deac0c;
    --gold-bottom: #b38613;
    --gold-glow: #f6c300;
    --gold-edge: #ad7b1f;
    --ink: #141008;
    --brand-back: #c99410;
  }
  * { margin: 0; padding: 0; box-sizing: border-box; }
  html, body {
    width: 1200px; height: 900px; overflow: hidden;
    background: var(--stage);
    font-family: "Source Sans 3", Arial, sans-serif;
  }
  .canvas { position: relative; width: 1200px; height: 900px; }

  .card {
    position: absolute; top: 275px;
    width: 477px; height: 293px; overflow: hidden;
  }
  .card--front {
    left: 116px;
    border-radius: 0 56px 0 56px;
    background: linear-gradient(180deg, var(--gold-top) 0%, var(--gold-mid) 45%, var(--gold-bottom) 100%);
    color: var(--ink);
  }
  .card--back {
    left: 622px;
    border-radius: 56px 0 56px 0;
    background: radial-gradient(ellipse 62% 78% at 44% 52%, var(--gold-glow) 0%, #e2ad0e 40%, var(--gold-edge) 100%);
  }

  .holder { position: absolute; right: 19px; top: 34px; text-align: right; }
  .holder__name { font-size: 20px; font-weight: 700; line-height: 1.1; }
  .holder__title { font-size: 13px; font-weight: 400; margin-top: 3px; }

  .brand { position: absolute; left: 28px; top: 84px; width: 270px; }
  .brand__name {
    font-size: 23px; font-weight: 700; line-height: 1.05;
    letter-spacing: 0.3px; color: var(--ink);
  }

  .address {
    position: absolute; right: 21px; top: 157px;
    text-align: right; font-size: 13.5px; line-height: 17px;
  }
  .contacts {
    position: absolute; right: 19px; top: 217px;
    list-style: none; font-size: 13.5px; line-height: 17.5px;
  }
  .contacts__item { display: flex; justify-content: flex-end; align-items: center; gap: 7px; }
  .contacts__icon { width: 11px; height: 11px; fill: var(--ink); flex: none; }

  .back-ornament {
    position: absolute; left: 40px; top: 10px;
    width: 330px; height: 300px; border-radius: 50%;
    background: radial-gradient(circle at 50% 55%, rgba(250,205,20,0.55) 0%, rgba(230,175,20,0.25) 55%, rgba(200,150,20,0) 75%);
  }
  .back-brand {
    position: absolute; left: 88px; top: 184px; width: 300px; text-align: center;
    font-size: 27px; font-weight: 700; line-height: 1.05;
    color: var(--brand-back); letter-spacing: 0.4px;
  }
</style>
</head>
<body>
<main class="canvas">
  <section class="card card--front" aria-label="Card front">
    <div class="holder">
      <p class="holder__name">Marcus Ellery</p>
      <p class="holder__title">Managing Director</p>
    </div>

    <div class="brand">
      <p class="brand__name">Golden Hour<br>Studio and Film</p>
    </div>

    <address class="address" style="font-style:normal">
      12345, Address Goes Here<br>
      Country Name, 123456
    </address>

    <ul class="contacts">
      <li class="contacts__item">044-123 456 789
        <svg class="contacts__icon" viewBox="0 0 24 24" aria-hidden="true"><path d="M6.6 10.8a15.1 15.1 0 0 0 6.6 6.6l2.2-2.2a1 1 0 0 1 1-.25 11.4 11.4 0 0 0 3.6.57 1 1 0 0 1 1 1V20a1 1 0 0 1-1 1A17 17 0 0 1 3 4a1 1 0 0 1 1-1h3.5a1 1 0 0 1 1 1c0 1.25.2 2.45.57 3.57a1 1 0 0 1-.25 1z"/></svg>
      </li>
      <li class="contacts__item">info@goldenhourfilm.net
        <svg class="contacts__icon" viewBox="0 0 24 24" aria-hidden="true"><path d="M2 5h20v14H2z M4 7v.4l8 5 8-5V7l-8 5z" fill-rule="evenodd"/></svg>
      </li>
      <li class="contacts__item">www.goldenhourfilm.net
        <svg class="contacts__icon" viewBox="0 0 24 24" aria-hidden="true"><path d="M10.6 13.4a1 1 0 0 1 0-1.4l4-4a1 1 0 1 1 1.4 1.4l-4 4a1 1 0 0 1-1.4 0zM7 21a4 4 0 0 1-2.8-6.8l3-3 1.4 1.4-3 3a2 2 0 1 0 2.8 2.8l3-3 1.4 1.4-3 3A4 4 0 0 1 7 21zm9.8-7.2-1.4-1.4 3-3a2 2 0 1 0-2.8-2.8l-3 3-1.4-1.4 3-3a4 4 0 0 1 5.6 5.6z"/></svg>
      </li>
    </ul>
  </section>

  <section class="card card--back" aria-label="Card back">
    <div class="back-ornament" role="img" aria-label="Large faint brand emblem decoration"></div>
    <p class="back-brand">Golden Hour<br>Studio and Film</p>
  </section>
</main>
</body>
</html>
```